New signage for apartment community in the Pacific Northwest

Signage for an apartment community in the Pacific Northwest. It should have a contemporary northwest vibe with a fresh exciting feeling. We are open to the colors cayenne, white, charcoal and a splash of lime green. Sign to have the name 'VOLTE' with the address number 28351 smaller underneath. sign can include a shape under the name or a feeling of energy in the shape of the name.

Target Market(s)

Young urban professionals

Industry/Entity Type

Real Estate Development

Requirements
Must have
• eyecatching
Should not have
• anything too cute or too busy

```html
<!DOCTYPE html>
<html lang="en">
<head>
<meta charset="utf-8">
<title>VOLTE Community Sign</title>
<link rel="stylesheet" href="https://fonts.googleapis.com/css2?family=Rye&family=Libre+Baskerville&display=swap">
<style>
  :root {
    --backdrop: #ecebe8;
    --charcoal-navy: #213342;
    --lime: #5dbb46;
    --outline: #231f20;
    --white: #ffffff;
  }
  html, body {
    margin: 0;
    padding: 0;
    width: 728px;
    height: 1200px;
    overflow: hidden;
    background: var(--backdrop);
  }
  .canvas {
    position: relative;
    width: 728px;
    height: 1200px;
  }
  .sign {
    position: absolute;
    left: 40px;
    top: 357px;
    width: 648px;
    height: 486px;
    display: block;
  }
  .sign-panel { fill: var(--charcoal-navy); }
  .sign-band { fill: var(--lime); }
  .sign-name {
    font-family: "Rye", serif;
    font-size: 300px;
    fill: var(--lime);
    stroke: var(--outline);
    stroke-width: 8px;
    paint-order: stroke fill;
  }
  .sign-number {
    font-family: "Libre Baskerville", serif;
    font-size: 104px;
    fill: var(--white);
  }
</style>
</head>
<body>
<main class="canvas">
  <svg class="sign" viewBox="0 0 1216 912" xmlns="http://www.w3.org/2000/svg" aria-label="VOLTE 28351 sign">
    <rect class="sign-panel" x="0" y="0" width="1216" height="912"/>
    <polygon class="sign-band" points="0,578 608,795 1216,578 1216,912 0,912"/>
    <text class="sign-name" x="608" y="420" text-anchor="middle" textLength="1070" lengthAdjust="spacingAndGlyphs">VOLTE</text>
    <text class="sign-number" x="608" y="548" text-anchor="middle" textLength="268" lengthAdjust="spacingAndGlyphs">28351</text>
  </svg>
</main>
</body>
</html>
```